At Home Pet Euthanasia - business cards & brand stationary

We already have a logo and the colors and a website. Need a business card designed that will be able to customized to multiple veterinarians who will be partnering with us. The feel needs to be compassionate, comforting with our tagline 'A Gift of Love at Home'. It will be 2 sides.
On the back our platform/partner vets will be customizing each business card with their own service areas, phone numbers, name and title. On the front, i would like to see experimentation with use of our photos, the logo, tagline and a description 'Peaceful and Compassionate At-Home Pet Euthanasia'

```html
<!DOCTYPE html>
<html lang="en">
<head>
<meta charset="utf-8">
<title>Hearthpaw business card</title>
<link href="https://fonts.googleapis.com/css2?family=Arimo:wght@400;700&family=Courgette&family=Quicksand:wght@400;700&display=swap" rel="stylesheet">
<style>
  :root {
    --backdrop: #d4d4d4;
    --brand-blue: #7598c0;
    --card-white: #ffffff;
    --ink: #111111;
  }
  * { box-sizing: border-box; margin: 0; padding: 0; }
  html, body { width: 1200px; height: 800px; overflow: hidden; }
  body {
    background: var(--backdrop);
    display: flex;
    align-items: center;
    justify-content: center;
    gap: 60px;
  }
  .card {
    position: relative;
    width: 500px;
    height: 286px;
    border-radius: 20px;
    overflow: hidden;
    flex: none;
  }

  /* Contact side */
  .card--contact { background: var(--card-white); font-family: "Arimo", Arial, sans-serif; }
  .contact-band { position: absolute; left: 0; top: 130px; width: 320px; height: 62px; background: var(--brand-blue); }
  .side-band { position: absolute; left: 440px; top: 58px; width: 60px; height: 40px; background: var(--brand-blue); }
  .brand-block {
    position: absolute; left: 310px; top: 44px; width: 140px; height: 140px;
    background: var(--brand-blue);
    display: flex; flex-direction: column; align-items: center; justify-content: center; gap: 10px;
  }
  .brand-block__dot { width: 22px; height: 22px; background: var(--card-white); }
  .brand-block__name { color: var(--card-white); font-family: "Quicksand", sans-serif; font-weight: 700; font-size: 24px; line-height: 1; }
  .holder { position: absolute; left: 40px; top: 56px; }
  .holder__name { color: var(--brand-blue); font-weight: 700; font-size: 24px; line-height: 1; }
  .holder__title { color: var(--ink); font-size: 15px; margin-top: 4px; }
  .contact-list { position: absolute; left: 70px; top: 136px; list-style: none; color: var(--card-white); font-size: 14px; line-height: 17px; }
  .contact-list li { display: flex; align-items: center; gap: 6px; }
  .contact-list svg { width: 12px; height: 12px; flex: none; }
  .address { position: absolute; left: 100px; top: 216px; color: var(--ink); font-size: 16px; line-height: 20px; }

  /* Brand side */
  .card--brand { background: var(--brand-blue); color: var(--card-white); }
  .lockup { position: absolute; left: 62px; top: 70px; display: flex; align-items: center; gap: 18px; }
  .lockup__mark { width: 50px; height: 50px; background: var(--card-white); flex: none; }
  .lockup__name { font-family: "Quicksand", sans-serif; font-weight: 700; font-size: 52px; line-height: 1; white-space: nowrap; }
  .tagline { position: absolute; left: 132px; top: 136px; font-family: "Quicksand", sans-serif; font-weight: 400; font-size: 20px; white-space: nowrap; }
  .service-line { position: absolute; left: 0; right: 0; bottom: 44px; text-align: center; font-family: "Courgette", cursive; font-size: 18px; white-space: nowrap; }
</style>
</head>
<body>
  <section class="card card--contact">
    <div class="contact-band"></div>
    <div class="side-band"></div>
    <div class="brand-block">
      <span class="brand-block__dot"></span>
      <span class="brand-block__name">Hearthpaw</span>
    </div>
    <div class="holder">
      <p class="holder__name">Daniel Marsh</p>
      <p class="holder__title">Managing Director</p>
    </div>
    <ul class="contact-list">
      <li><svg viewBox="0 0 12 12"><path d="M3 1 L5 3.5 L4 5 Q5 7 7 8 L8.5 7 L11 9 L9.5 11 Q5 11 1 5.5 Q1 2.5 3 1 Z" fill="#fff"/></svg>044-555 010 234</li>
      <li><svg viewBox="0 0 12 12"><rect x="0.5" y="2.5" width="11" height="7" fill="none" stroke="#fff"/><path d="M0.5 2.5 L6 7 L11.5 2.5" fill="none" stroke="#fff"/></svg>info@hearthpaw.com</li>
      <li><svg viewBox="0 0 12 12"><circle cx="6" cy="6" r="5.3" fill="none" stroke="#fff"/><ellipse cx="6" cy="6" rx="2.3" ry="5.3" fill="none" stroke="#fff"/><path d="M0.7 6 H11.3" stroke="#fff"/></svg>www.hearthpaw.com</li>
    </ul>
    <p class="address">421, Address line goes here<br>45452, Country Name</p>
  </section>

  <section class="card card--brand">
    <div class="lockup">
      <div class="lockup__mark"></div>
      <span class="lockup__name">Hearthpaw</span>
    </div>
    <p class="tagline">A gift of love at home.</p>
    <p class="service-line">Peaceful and Compassionate At-Home Pet Euthanasia</p>
  </section>
</body>
</html>
```